Adult Literacy Program - flyer to attract volunteers and students

We want a flyer that is engaging, colorful, modern and will appeal to our primary audience of adults aged 40-60. We are trying to attract both prospective volunteers (typically age 50+, mostly women) and students (typically aged 40+).
The flyer should feature diverse people working together in pairs of two, reading or talking, with a workbook or some reading material in front of them.

Our organization trains tutors to work one-on-one with adults who are learning how to read. Most of our adult students are non-native speakers of English. Many are of Haitian or Hispanic origin, so we would like some people who represent that demographic.

The Flyer should represent reading, learning, literacy, knowledge, growth,
and opportunities.
Our students are learning to read so they can advance their job opportunities.

Target Market(s)

Adults aged 40-60, primarily women, retired, volunteers

Industry/Entity Type

Education

Font styles to use
Serif
Sans Serif

Colors

Designer to choose colors to be used in the design.

Requirements
Must have
• - UPDATE: Should be designed as a TRI-FOLD brochure on 8.5 x 11 inch paper that will be folded into thirds.
• - Images of diverse people, women and men, who look Hispanic, Haitian and other nationalities as well as Caucasian.
• - Our logo on the front cover
Nice to have
• The sample flyer is very boring and dry! We are open to different ways of presenting the text.

```html
<!DOCTYPE html>
<html lang="en">
<head>
<meta charset="utf-8">
<title>Volunteer Tri-fold Brochure</title>
<link rel="stylesheet" href="https://fonts.googleapis.com/css2?family=Lato:ital,wght@0,400;0,700;0,900;1,400;1,700;1,900&display=swap">
<style>
  :root {
    --navy: #1f2a6b;
    --sky: #1ba6dc;
    --sky-light: #3dbde8;
    --ice: #8fdcf5;
    --white: #ffffff;
    --paper: #ececec;
  }
  * { box-sizing: border-box; margin: 0; padding: 0; }
  html, body { width: 896px; height: 1200px; overflow: hidden; }
  body { background: var(--paper); font-family: "Lato", sans-serif; position: relative; }
  .sheet { position: absolute; left: 88px; width: 720px; height: 556px; overflow: hidden; box-shadow: 0 4px 14px rgba(0,0,0,.18); }
  .sheet--outside { top: 30px; }
  .sheet--inside { top: 614px; }
  .sheet__art { position: absolute; inset: 0; width: 720px; height: 556px; }
  .block { position: absolute; }

  /* outside */
  .headline { left: 262px; top: 262px; width: 250px; color: var(--navy); font-weight: 900; font-size: 27px; line-height: 1.05; }
  .contact-lead { left: 262px; top: 330px; width: 230px; color: var(--white); font-weight: 900; font-size: 17px; line-height: 1.1; }
  .contact-list { left: 262px; top: 378px; width: 260px; color: var(--white); font-size: 12.5px; line-height: 1.35; }
  .contact-email { margin-top: 6px; color: var(--navy); font-weight: 700; }
  .contact-email span { color: var(--white); }
  .web-pill { left: 262px; top: 470px; background: var(--white); color: var(--navy); font-weight: 900; font-size: 15px; padding: 6px 16px; border-radius: 0 12px 0 12px; }
  .brand { left: 596px; top: 166px; width: 92px; height: 48px; text-align: center; color: var(--navy); font-weight: 900; font-size: 10.5px; line-height: 1.15; display: flex; align-items: center; justify-content: center; }
  .tag-volunteer { left: 512px; top: 264px; width: 208px; background: var(--white); color: var(--navy); font-weight: 900; font-size: 27px; letter-spacing: .3px; padding: 5px 0 5px 20px; border-radius: 22px 0 0 22px; }
  .enrich { left: 540px; top: 322px; color: var(--ice); font-size: 17px; }
  .help { left: 540px; top: 352px; width: 160px; color: var(--white); font-size: 15px; line-height: 1.15; }

  /* inside */
  .panel-title { font-weight: 900; font-style: italic; color: var(--navy); font-size: 23px; line-height: 1.1; }
  .tutors { left: 24px; top: 196px; width: 200px; }
  .students { left: 500px; top: 24px; width: 205px; }
  .list { list-style: none; margin-top: 4px; color: var(--white); font-size: 9.5px; line-height: 1.4; font-style: italic; }
  .list li { padding-left: 10px; position: relative; }
  .list li::before { content: ""; position: absolute; left: 0; top: 5px; width: 4px; height: 4px; border-radius: 50%; background: var(--white); }
  .list .sub { padding-left: 22px; }
  .list .sub::before { left: 12px; }
  .list .plain { padding-left: 0; }
  .list .plain::before { display: none; }
  .tutors-pledge { left: 24px; top: 372px; width: 205px; color: var(--navy); font-weight: 900; font-style: italic; font-size: 20px; line-height: 1.1; }
  .students-pledge { left: 560px; top: 212px; width: 140px; color: var(--navy); font-weight: 900; font-style: italic; font-size: 18px; line-height: 1.1; text-align: right; }
</style>
</head>
<body>

<section class="sheet sheet--outside" aria-label="Brochure outside">
  <svg class="sheet__art" viewBox="0 0 720 556">
    <defs>
      <linearGradient id="photoWarm" x1="0" y1="0" x2="1" y2="1">
        <stop offset="0" stop-color="#8a7a6a"/><stop offset=".5" stop-color="#9fb3cc"/><stop offset="1" stop-color="#c23045"/>
      </linearGradient>
      <linearGradient id="photoLibrary" x1="0" y1="0" x2="1" y2="1">
        <stop offset="0" stop-color="#3a2a22"/><stop offset=".6" stop-color="#6c7f90"/><stop offset="1" stop-color="#d8d6d0"/>
      </linearGradient>
      <clipPath id="outsideClip"><rect width="720" height="556"/></clipPath>
    </defs>
    <g clip-path="url(#outsideClip)">
      <rect width="720" height="556" fill="var(--navy)"/>
      <rect x="8" y="10" width="228" height="536" fill="url(#photoWarm)" role="img" aria-label="Photo: a tutor and an adult student reading together at a library table"/>
      <rect x="242" y="10" width="470" height="230" fill="url(#photoLibrary)" role="img" aria-label="Photo: two smiling women with a book in a library"/>
      <circle cx="420" cy="360" r="232" fill="var(--sky)" stroke="var(--navy)" stroke-width="8"/>
      <rect x="236" y="0" width="6" height="556" fill="var(--navy)"/>
      <circle cx="800" cy="430" r="260" fill="var(--navy)"/>
      <circle cx="642" cy="190" r="50" fill="var(--white)" stroke="var(--navy)" stroke-width="4"/>
    </g>
  </svg>

  <div class="block brand">Reading Bridge Friends</div>

  <h1 class="block headline">You can make<br>a difference!</h1>
  <p class="block contact-lead">Contact us today<br>to learn more.</p>
  <div class="block contact-list">
    <p>Volunteer Desk: 555-014-2286</p>
    <p>Cedar Glen, Marlow &amp; South Point:</p>
    <p>555-016-9174</p>
    <p class="contact-email">email: <span>literacy@harborlibrary.org</span></p>
  </div>
  <div class="block web-pill">harborlibrary.org/literacy</div>

  <div class="block tag-volunteer">VOLUNTEER</div>
  <p class="block enrich">Enrich a Life!</p>
  <p class="block help">Help an adult learn to read, write or speak English</p>
</section>

<section class="sheet sheet--inside" aria-label="Brochure inside">
  <svg class="sheet__art" viewBox="0 0 720 556">
    <defs>
      <linearGradient id="photoGroup" x1="0" y1="0" x2="1" y2="1">
        <stop offset="0" stop-color="#4a3a34"/><stop offset=".5" stop-color="#8fa0b4"/><stop offset="1" stop-color="#d9d3c8"/>
      </linearGradient>
      <linearGradient id="photoPair" x1="0" y1="0" x2="1" y2="1">
        <stop offset="0" stop-color="#bfb6aa"/><stop offset="1" stop-color="#55708a"/>
      </linearGradient>
      <linearGradient id="photoDesk" x1="0" y1="0" x2="1" y2="0">
        <stop offset="0" stop-color="#d8cfc4"/><stop offset=".6" stop-color="#9aa6b2"/><stop offset="1" stop-color="#3c3a40"/>
      </linearGradient>
      <clipPath id="insideClip"><rect width="720" height="556"/></clipPath>
    </defs>
    <g clip-path="url(#insideClip)">
      <rect width="720" height="556" fill="var(--navy)"/>
      <rect x="8" y="10" width="704" height="536" fill="var(--sky)"/>
      <path d="M0 130 C 200 140, 262 240, 262 556 L0 556 Z" fill="var(--sky-light)" stroke="var(--navy)" stroke-width="8"/>
      <path d="M720 10 L 478 10 C 440 160, 470 380, 720 390 Z" fill="var(--sky-light)" stroke="var(--navy)" stroke-width="8"/>
      <circle cx="300" cy="20" r="200" fill="url(#photoGroup)" stroke="var(--navy)" stroke-width="8" role="img" aria-label="Photo: a smiling woman and a group of adult learners studying at a library table"/>
      <circle cx="560" cy="650" r="250" fill="url(#photoDesk)" stroke="var(--navy)" stroke-width="8" role="img" aria-label="Photo: a woman writing and a man reading a book at a desk"/>
      <circle cx="360" cy="330" r="80" fill="url(#photoPair)" stroke="var(--navy)" stroke-width="6" role="img" aria-label="Photo: an older man and a woman reading a workbook together"/>
    </g>
  </svg>

  <div class="block tutors">
    <h2 class="panel-title">Tutors</h2>
    <ul class="list">
      <li>No special skills or degrees needed — just a degree of caring!</li>
      <li>Training offered throughout the year</li>
      <li>Tutors meet students weekly at a library</li>
      <li>Instructional materials provided</li>
      <li>Ongoing support available</li>
    </ul>
  </div>
  <p class="block tutors-pledge">Teach an adult to read and you'll change a life forever.</p>

  <div class="block students">
    <h2 class="panel-title">Students</h2>
    <ul class="list">
      <li class="plain">Students are adults in need of</li>
      <li class="sub">basic literacy skills</li>
      <li class="sub">pre-diploma skills</li>
      <li class="sub">conversational English</li>
      <li>Tutoring is free of charge</li>
      <li>Tutoring is one-on-one</li>
      <li>Flexible scheduling during library hours</li>
      <li>Lessons focus on student goals</li>
    </ul>
  </div>
  <p class="block students-pledge">If you can read, you can tutor!</p>
</section>

</body>
</html>
```